Business Card Design needed for start up company Halvora

In need of a new business card designed for a start up company based in Sydney, Halvora is a new start up innovative Company, our mission it to make property accessible for everyday Australian and to become the leading Real Estate platform in Australia. We want it to be fresh and clean.

Industry/Entity Type

Financial

Contact Information for Business Card

Section for Name
Section for Title

HALVORA - The Strength of Pooling
Mobile:
Direct:

Font styles to use
Sans Serif

Colors
33a6d7
0692cd
0255a3
ffffff

Requirements
Must have
• Logo, all business card details

```html
<!DOCTYPE html>
<html lang="en">
<head>
<meta charset="utf-8">
<title>Halvora business card</title>
<link rel="stylesheet" href="https://fonts.googleapis.com/css2?family=Montserrat:wght@800&family=Jost:wght@400;600&display=swap">
<style>
  :root {
    --sky: #33a6d7;
    --azure: #0692cd;
    --navy: #0255a3;
    --deep: #1f3f80;
    --white: #ffffff;
    --paper: #f3f4f5;
    --stage: #e6e8eb;
  }
  * { margin: 0; padding: 0; box-sizing: border-box; }
  html, body { width: 1200px; height: 911px; overflow: hidden; }
  body { background: var(--stage); position: relative; font-family: "Jost", sans-serif; }

  .card {
    position: absolute;
    width: 640px;
    height: 366px;
    border-radius: 22px;
    overflow: hidden;
    box-shadow: 0 10px 24px rgba(0,0,0,.18);
  }
  .card--front { left: 60px; top: 60px; background: var(--paper); }
  .card--back { left: 500px; top: 485px; background: var(--sky); }

  .card__wave { position: absolute; inset: 0; width: 100%; height: 100%; }

  .brand { position: absolute; display: flex; align-items: center; gap: 10px; }
  .brand__dot { border-radius: 50%; flex: none; }
  .brand__name { font-family: "Montserrat", sans-serif; font-weight: 800; letter-spacing: -1px; line-height: 1; }

  .card--front .brand { left: 44px; bottom: 112px; }
  .card--front .brand__dot { width: 42px; height: 42px; background: var(--azure); }
  .card--front .brand__name { font-size: 40px; color: var(--deep); }

  .card--back .brand { left: 70px; top: 120px; }
  .card--back .brand__dot { width: 70px; height: 70px; background: var(--white); }
  .card--back .brand__name { font-size: 76px; color: var(--white); }

  .tagline {
    position: absolute; left: 152px; top: 220px;
    color: var(--white); font-size: 17px; font-style: italic;
  }

  .contact {
    position: absolute; right: 36px; top: 46px;
    text-align: right; color: var(--white);
    font-size: 15px; line-height: 1.5;
  }
  .contact__name { color: var(--sky); font-weight: 600; font-size: 22px; letter-spacing: .5px; line-height: 1.2; }
  .contact__title { font-size: 16px; margin-bottom: 14px; }
  .contact__address { margin-bottom: 14px; }
  .contact__row { display: flex; justify-content: flex-end; align-items: center; gap: 10px; }
  .contact__icon { width: 14px; height: 14px; flex: none; }
</style>
</head>
<body>

<section class="card card--front" aria-label="Card front">
  <svg class="card__wave" viewBox="0 0 640 366" preserveAspectRatio="none" aria-hidden="true">
    <defs>
      <linearGradient id="navyFade" x1="0" y1="0" x2="1" y2="1">
        <stop offset="0" stop-color="#3d63a3"/>
        <stop offset="1" stop-color="#1c3d80"/>
      </linearGradient>
    </defs>
    <path d="M120 366 C 240 332, 352 292, 402 200 C 378 294, 300 342, 236 366 Z" fill="var(--sky)"/>
    <path d="M330 0 C 282 70, 408 150, 366 236 C 334 292, 266 330, 244 366 L640 366 L640 0 Z" fill="url(#navyFade)"/>
  </svg>

  <div class="brand">
    <span class="brand__dot"></span>
    <span class="brand__name">HALVORA</span>
  </div>

  <div class="contact">
    <div class="contact__name">MARA ELLISON</div>
    <div class="contact__title">CEO/FOUNDER</div>
    <div class="contact__address">42 Wattle Street<br>Sydney, NSW 2000</div>
    <div class="contact__row">612 555 0148
      <svg class="contact__icon" viewBox="0 0 16 16" aria-hidden="true"><path d="M4 1 L6.5 4 L5 6 C6 8.5 7.5 10 10 11 L12 9.5 L15 12 L13 15 C7 14.5 1.5 9 1 3 Z" fill="var(--white)"/></svg>
    </div>
    <div class="contact__row">612 555 0172
      <svg class="contact__icon" viewBox="0 0 16 16" aria-hidden="true"><rect x="4" y="1" width="8" height="14" rx="1.5" fill="none" stroke="var(--white)" stroke-width="1.6"/><circle cx="8" cy="12.5" r="0.9" fill="var(--white)"/></svg>
    </div>
    <div class="contact__row">mara@halvora.com
      <svg class="contact__icon" viewBox="0 0 16 16" aria-hidden="true"><rect x="1" y="3" width="14" height="10" rx="1" fill="var(--white)"/><path d="M1.5 3.5 L8 9 L14.5 3.5" fill="none" stroke="var(--deep)" stroke-width="1.2"/></svg>
    </div>
    <div class="contact__row">www.halvora.com
      <svg class="contact__icon" viewBox="0 0 16 16" aria-hidden="true"><circle cx="8" cy="8" r="6.5" fill="none" stroke="var(--white)" stroke-width="1.5"/><path d="M1.5 8 H14.5 M8 1.5 C5 5 5 11 8 14.5 M8 1.5 C11 5 11 11 8 14.5" fill="none" stroke="var(--white)" stroke-width="1.1"/></svg>
    </div>
  </div>
</section>

<section class="card card--back" aria-label="Card back">
  <div class="brand">
    <span class="brand__dot"></span>
    <span class="brand__name">HALVORA</span>
  </div>
  <p class="tagline">The Strength of Pooling</p>
</section>

</body>
</html>
```